Ridgeline Haul Carriers - Website

A clean, not cluttered informative website for our business. We specialize in the transportation of radioactive materials across North America. The site is mostly for information about our company and will not be used to attract business but will be used to attract employee's mainly drivers. Driver's are very hard to find in our area. One of the pages needs to be a job's posting page with an apply now button. Either an application can be filled out there or a resume can be uploaded which ever functionality works better. I would like a website that I can easily edit, ability to change text and photos.

Number of Pages Required

5+ page

Colors

Designer to choose colors to be used in the design.

Requirements
Must have
• Home - About - Services - Jobs - Contact pages
• A way prospective employee's can apply or upload their resume to be emailed to me
• Very clean apperance
Should not have
• I don't want it to be busy

```html
<!DOCTYPE html>
<html lang="en">
<head>
<meta charset="utf-8">
<title>Ridgeline Haul Carriers</title>
<link href="https://fonts.googleapis.com/css2?family=Montserrat:wght@600;700;800&family=Open+Sans:wght@400;600;700&display=swap" rel="stylesheet">
<style>
:root{
  --red:#e30613;
  --red-dark:#c10510;
  --ink:#1c1c1c;
  --text:#666;
  --muted:#8a8a8a;
  --blue:#1565c0;
  --black:#0d0d0d;
  --line:#e2e2e2;
  --white:#fff;
}
*{box-sizing:border-box;margin:0;padding:0}
html,body{width:1200px;height:4296px;overflow:hidden}
body{position:relative;background:var(--white);font-family:"Open Sans",Arial,sans-serif;color:var(--text)}
.abs{position:absolute}
.heading{font-family:"Montserrat",Arial,sans-serif;font-weight:800;color:var(--ink);text-align:center;font-size:44px;letter-spacing:.5px}
.body-copy{font-size:14px;line-height:27px;text-align:center;color:var(--text)}
.btn{display:inline-flex;align-items:center;gap:8px;background:var(--red);color:var(--white);font-family:"Montserrat",Arial,sans-serif;font-weight:700;font-size:16px;text-transform:uppercase;border-radius:3px;padding:0 24px;height:46px}
.btn .dot{width:14px;height:14px;border-radius:50%;background:var(--white);position:relative}
.btn .dot::after{content:"";position:absolute;left:5px;top:4px;border-left:5px solid var(--red);border-top:3px solid transparent;border-bottom:3px solid transparent}

/* top bar */
.topbar{left:0;top:0;width:1200px;height:44px;background:var(--black);color:#ddd;font-size:13px}
.topbar .contact{position:absolute;left:112px;top:0;line-height:44px;display:flex;gap:18px;align-items:center}
.topbar .apply{position:absolute;right:36px;top:0;width:164px;height:44px;background:var(--red);color:var(--white);font-family:"Montserrat",sans-serif;font-weight:700;font-size:15px;display:flex;align-items:center;justify-content:center}
/* header */
.header{left:0;top:44px;width:1200px;height:114px;background:var(--white)}
.logo{font-family:"Montserrat",sans-serif;font-weight:800;color:var(--red);line-height:1;text-transform:uppercase}
.header .logo{position:absolute;left:112px;top:36px;font-size:26px}
.header .logo small{display:block;font-size:13px;letter-spacing:6px;margin-top:6px}
.nav{position:absolute;right:112px;top:0;height:114px;display:flex;align-items:center;gap:34px;font-family:"Montserrat",sans-serif;font-weight:600;font-size:15px;color:#333;text-transform:uppercase}
/* hero */
.hero{left:0;top:158px;width:1200px;height:572px;background:linear-gradient(180deg,#8a8c8e 0%,#6f7376 45%,#4d5356 100%)}
.hero h1{position:absolute;top:192px;width:100%;text-align:center;font-family:"Montserrat",sans-serif;font-weight:800;font-size:40px;color:var(--white);text-transform:uppercase}
.hero p{position:absolute;top:256px;left:300px;width:600px;text-align:center;color:var(--white);font-size:16px;line-height:28px;font-weight:600}
.hero .btn{position:absolute;left:504px;top:338px}
.dots{position:absolute;top:486px;left:528px;display:flex;gap:14px}
.dots span{width:18px;height:18px;border-radius:50%;border:2px solid var(--white)}
.dots span.on{background:var(--white)}
/* services */
.services-title{top:820px;left:0;width:1200px}
.services-text{top:916px;left:200px;width:800px}
.services-wave{left:0;top:1370px}
.video{left:246px;top:1165px;width:708px;height:373px;background:linear-gradient(135deg,#3a5f8c,#7d9ab8 50%,#2f3b4a);border:4px solid var(--white);box-shadow:0 4px 18px rgba(0,0,0,.3)}
.play{position:absolute;left:330px;top:162px;width:48px;height:48px;border-radius:50%;background:var(--red)}
.play::after{content:"";position:absolute;left:19px;top:14px;border-left:15px solid var(--white);border-top:10px solid transparent;border-bottom:10px solid transparent}
.features{top:1610px;left:0;width:1200px;display:flex;justify-content:center;gap:120px;color:var(--white);font-family:"Montserrat",sans-serif;font-weight:600;font-size:23px}
.feature{display:flex;align-items:center;gap:18px}
/* mission */
.mission-bg{left:0;top:1753px;width:1200px;height:560px;background:linear-gradient(180deg,#f6f6f6,#fff)}
.mission-photo{left:115px;top:1882px;width:455px;height:323px;background:linear-gradient(180deg,#9bb7d8 0%,#c8d6e4 55%,#5f7a4a 56%,#4a6238 100%)}
.mission-card{left:527px;top:1927px;width:561px;height:233px;background:var(--white);box-shadow:0 2px 14px rgba(0,0,0,.15);padding:40px 40px}
.mission-card h2{font-family:"Montserrat",sans-serif;font-weight:800;font-size:40px;color:var(--ink);margin-bottom:20px}
.mission-card p{font-size:14px;line-height:27px;text-align:justify}
.divider{left:112px;top:2325px;width:976px;height:1px;background:var(--line)}
/* area */
.area-title{top:2413px;left:0;width:1200px}
.area-text{top:2490px;left:270px;width:660px}
.area-card{top:2580px;width:302px;height:220px}
.area-card .photo{height:164px}
.area-card .label{height:56px;background:var(--blue);color:var(--white);font-family:"Montserrat",sans-serif;font-weight:700;font-size:25px;display:flex;align-items:center;justify-content:center;text-transform:uppercase}
.area-card.us .label{background:var(--red)}
/* drivers */
.drivers{left:0;top:2912px;width:1200px;height:490px}
.drivers h2{position:absolute;left:624px;top:60px;font-family:"Montserrat",sans-serif;font-weight:800;font-size:40px;line-height:52px;color:var(--white);text-transform:uppercase}
.drivers p{position:absolute;left:624px;width:470px;font-size:14px;line-height:24px;color:var(--white)}
.drivers .btn{position:absolute;left:624px;top:374px;background:var(--blue);height:44px;font-size:15px}
/* clients */
.clients-title{top:3498px;left:0;width:1200px}
.clients-text{top:3582px;left:330px;width:540px}
.client{top:3674px;width:184px;height:78px;background:var(--white);border:1px solid var(--line);box-shadow:0 1px 6px rgba(0,0,0,.08);display:flex;align-items:center;justify-content:center;gap:8px;font-family:"Montserrat",sans-serif;font-weight:700;font-size:15px;color:#333}
.client i{width:14px;height:14px;border-radius:50%;background:#333}
.client.active{border-bottom:4px solid var(--red)}
.arrow{top:3700px;width:14px;height:14px;border-left:2px solid #555;border-bottom:2px solid #555}
/* footer */
.footer-curve{left:0;top:3840px}
.footer{left:0;top:3960px;width:1200px;height:336px;background:var(--black);color:#ccc}
.footer .logo{position:absolute;left:115px;top:44px;color:var(--white);font-size:26px}
.footer .logo small{display:block;font-size:13px;letter-spacing:6px;margin-top:6px}
.social{position:absolute;left:130px;top:132px;display:flex;gap:12px}
.social span{width:20px;height:20px;border-radius:50%;background:var(--white)}
.fcol{position:absolute;top:38px}
.fcol h4{font-family:"Montserrat",sans-serif;font-weight:700;font-size:16px;color:var(--white);text-transform:uppercase;margin-bottom:18px}
.fcol li{list-style:none;font-size:13px;line-height:26px;color:#ddd;position:relative;padding-left:22px}
.fcol li::before{content:"";position:absolute;left:2px;top:10px;width:5px;height:5px;border-right:2px solid #ddd;border-top:2px solid #ddd;transform:rotate(45deg)}
.fcol li::after{content:"";position:absolute;left:7px;top:10px;width:5px;height:5px;border-right:2px solid #ddd;border-top:2px solid #ddd;transform:rotate(45deg)}
.footer .rule{position:absolute;left:112px;top:256px;width:976px;height:1px;background:#444}
.copyright{position:absolute;top:286px;width:100%;text-align:center;font-size:13px;color:#ddd}
.chat{position:absolute;left:945px;top:296px;width:157px;height:40px;background:var(--red);color:var(--white);font-family:"Montserrat",sans-serif;font-weight:700;font-size:15px;display:flex;align-items:center;justify-content:center;gap:8px;text-transform:uppercase}
.chat i{width:14px;height:11px;border-radius:6px;background:var(--white)}
.tag{position:absolute;right:22px;top:306px;font-size:12px;color:#bbb}
</style>
</head>
<body>

<div class="abs topbar">
  <div class="contact">
    <span>&#9742;&nbsp; (555) 214-7730</span><span>|</span><span>&#9993;&nbsp; hello@ridgelinehaul.com</span>
  </div>
  <div class="apply">APPLY NOW</div>
</div>

<header class="abs header">
  <div class="logo">Ridgeline<small>Haul Carriers</small></div>
  <nav class="nav">
    <span>Home</span><span>About Us</span><span>Services</span><span>Jobs</span><span>Contact Us</span>
    <svg width="16" height="16" viewBox="0 0 16 16"><circle cx="6.5" cy="6.5" r="5" fill="none" stroke="#333" stroke-width="2"/><line x1="10.5" y1="10.5" x2="15" y2="15" stroke="#333" stroke-width="2"/></svg>
  </nav>
</header>

<section class="abs hero" role="img" aria-label="Photo of a tractor unit hauling a tanker trailer on a wet yard">
  <h1>Ridgeline Haul Carriers</h1>
  <p>We specialize in both expedited and regular LTL, Partial Load and Full Truck Load service between Canada, the USA and Mexico.</p>
  <span class="btn">Read More <span class="dot"></span></span>
  <div class="dots"><span></span><span></span><span class="on"></span><span></span><span></span></div>
</section>

<h2 class="abs heading services-title">OUR SERVICES</h2>
<div class="abs body-copy services-text">
  <p>Ridgeline Haul Carriers, we specialize in both expedited and regular LTL, Partial Load and Full Truck Load service between Canada, the USA and Mexico.</p>
  <p style="margin-top:26px">Our operations staff monitor transit times for every shipment with our satellite tracking and communications network installed in every power unit. We only use 53' high cube air ride logistic van trailers for our dry freight as well as 53' single drop air ride flatbeds. To compliment our service, we contact each consignee to ensure delivery date and adjust to any other needs required for your total satisfaction.</p>
</div>

<svg class="abs services-wave" width="1200" height="383" viewBox="0 0 1200 383">
  <path d="M0 0 Q600 230 1200 0 L1200 383 L0 383 Z" fill="var(--red)"/>
  <path d="M0 40 Q600 250 1200 40 L1200 383 L0 383 Z" fill="var(--red-dark)" opacity=".35"/>
</svg>

<div class="abs video" role="img" aria-label="Video still of a driver standing in front of a blue truck">
  <span class="play"></span>
</div>

<div class="abs features">
  <div class="feature">
    <svg width="66" height="46" viewBox="0 0 66 46" fill="none" stroke="#fff" stroke-width="3"><rect x="2" y="6" width="38" height="28"/><path d="M40 14h14l10 12v8H40z"/><circle cx="14" cy="38" r="5"/><circle cx="52" cy="38" r="5"/><path d="M12 20l6 6 12-12"/></svg>
    Direct Delivery
  </div>
  <div class="feature">
    <svg width="52" height="52" viewBox="0 0 52 52" fill="none" stroke="#fff" stroke-width="3"><path d="M30 4a9 9 0 0 1 9 9c0 7-9 16-9 16s-9-9-9-16a9 9 0 0 1 9-9z"/><circle cx="30" cy="13" r="3"/><rect x="4" y="32" width="22" height="12"/><circle cx="10" cy="47" r="3"/><circle cx="22" cy="47" r="3"/></svg>
    Tracking &amp; Tracing
  </div>
  <div class="feature">
    <svg width="52" height="52" viewBox="0 0 52 52" fill="none" stroke="#fff" stroke-width="3"><rect x="8" y="4" width="36" height="44"/><line x1="16" y1="16" x2="36" y2="16"/><line x1="16" y1="24" x2="36" y2="24"/><line x1="16" y1="32" x2="30" y2="32"/></svg>
    Online POD
  </div>
</div>

<div class="abs mission-bg"></div>
<div class="abs mission-photo" role="img" aria-label="Photo of a white tanker truck on a country road"></div>
<div class="abs mission-card">
  <h2>OUR MISSION</h2>
  <p>With a firm commitment to superior service and integrity above all, the team has developed an enviable reputation within the transportation industry.</p>
</div>

<div class="abs divider"></div>

<h2 class="abs heading area-title">SERVICE AREA</h2>
<p class="abs body-copy area-text">Ridgeline Haul Carriers, we specialize in both expedited and regular LTL, Partial Load and Full Truck Load service between Canada, the USA and Mexico.</p>

<div class="abs area-card" style="left:112px">
  <div class="photo" role="img" aria-label="Photo of a Canadian city skyline" style="background:linear-gradient(180deg,#9cc3e6,#6c8aa6 60%,#8a6a52)"></div>
  <div class="label">Canada</div>
</div>
<div class="abs area-card us" style="left:450px">
  <div class="photo" role="img" aria-label="Photo of an American city skyline at sunset" style="background:linear-gradient(180deg,#d9a36a,#7a6a64 55%,#3c4656)"></div>
  <div class="label">United States</div>
</div>
<div class="abs area-card" style="left:788px">
  <div class="photo" role="img" aria-label="Photo of a Mexican city skyline" style="background:linear-gradient(180deg,#8fb8e0,#6f8aa8 60%,#4f6a5a)"></div>
  <div class="label">Mexico</div>
</div>

<section class="abs drivers">
  <svg class="abs" style="left:0;top:0" width="1200" height="490" viewBox="0 0 1200 490">
    <defs><linearGradient id="driverPhoto" x1="0" y1="0" x2="1" y2="1"><stop offset="0" stop-color="#d7c6b4"/><stop offset=".5" stop-color="#a88466"/><stop offset="1" stop-color="#5c4a3e"/></linearGradient></defs>
    <rect width="1200" height="490" fill="var(--red)"/>
    <polygon points="0,0 520,0 590,490 0,490" fill="url(#driverPhoto)" role="img" aria-label="Photo of a smiling driver at the wheel of a truck"/>
  </svg>
  <h2>We are looking for<br>company drivers</h2>
  <p style="top:200px">We're looking for Company Drivers who want a better life. Drivers who want money in their pocket, and home-time to spend it!!!</p>
  <p style="top:256px">Due to expansion, this Port Aldene, Ontario based international Truckload carrier servicing Canada and all 48 States, has openings and great opportunities for Company Drivers with a desire to succeed.</p>
  <span class="btn">Apply Now <span class="dot"></span></span>
</section>

<h2 class="abs heading clients-title">OUR CLIENTS</h2>
<p class="abs body-copy clients-text">Nemo enim ipsam voluptatem quia voluptas sit aspernatur aut odit aut fugit, sed quia consequuntur magni dolores eos qui ratione voluptatem sequi nesciunt.</p>

<span class="abs arrow" style="left:60px;transform:rotate(45deg)"></span>
<div class="abs client" style="left:104px"><i></i>Brightwell Foods</div>
<div class="abs client" style="left:304px">Corvane Labs</div>
<div class="abs client active" style="left:504px">Tidewater Drinks</div>
<div class="abs client" style="left:706px">Halden Pharma</div>
<div class="abs client" style="left:910px">Novaline</div>
<span class="abs arrow" style="left:1128px;transform:rotate(-135deg)"></span>

<svg class="abs footer-curve" width="1200" height="130" viewBox="0 0 1200 130">
  <path d="M0 126 Q600 -6 1200 126" fill="none" stroke="var(--red)" stroke-width="6"/>
  <path d="M0 130 Q600 10 1200 130 Z" fill="var(--black)"/>
</svg>

<footer class="abs footer">
  <div class="logo">Ridgeline<small>Haul Carriers</small></div>
  <div class="social" aria-label="Social links"><span></span><span></span><span></span><span></span><span></span><span></span></div>
  <div class="fcol" style="left:490px">
    <h4>Quick Links</h4>
    <ul><li>Home</li><li>About Us</li><li>Services</li><li>Employment</li><li>Contact Us</li></ul>
  </div>
  <div class="fcol" style="left:730px">
    <h4>Resources</h4>
    <ul><li>Company Drivers</li><li>Owner/Operators</li><li>Service Area</li><li>Terms Of Services</li><li>Rate Quote</li></ul>
  </div>
  <div class="fcol" style="left:994px">
    <h4>Language</h4>
    <ul><li>English</li><li>Turkish</li><li>Spanish</li></ul>
  </div>
  <div class="rule"></div>
  <p class="copyright">© Copyright 2019 Ridgeline Haul Carriers. All Rights Reserved &nbsp;&nbsp;|&nbsp;&nbsp; Privacy Policy</p>
  <div class="chat"><i></i>Live Chat</div>
  <span class="tag">C10</span>
</footer>

</body>
</html>
```